Travel Agency Website - Simple General

Need a 7 page simple design that is pretty repetitive. Need to be able to load quickly that is SEO optimized. Trying to give ideas on what they can do, be personal as we are local, but at the same time come across as professional and get information easily with little burden.

- Landing Page
- Brimwell Vacations Page
- Family Trips
- Road Trips from Texas
- Other Destinations
- About Us Page
- Contact Us Page

Target Market(s)

Families

Coding

Coded - Design and coding required

Number of Pages Required

5+ page

Colors

Designer to choose colors to be used in the design.

Requirements
Must have
• Like it to flow easily with our logo. Use that for colors, etc.

```html
<!DOCTYPE html>
<html lang="en">
<head>
<meta charset="utf-8">
<title>Ramble &amp; Rove – Landing Page Hover States</title>
<link href="https://fonts.googleapis.com/css2?family=Outfit:wght@400;500;600;700;800&display=swap" rel="stylesheet">
<style>
:root{
  --board:#9a9a9a;
  --white:#ffffff;
  --teal:#2b6b6c;
  --teal-glass:rgba(38,104,106,.82);
  --teal-dark:#1f5556;
  --gold:#c99a4e;
  --gold-dark:#b5853a;
  --cream:#f7f1e7;
  --ink:#1f4344;
  --nav-text:#2a4a4b;
}
*{box-sizing:border-box;margin:0;padding:0}
html,body{width:1200px;height:1126px;overflow:hidden}
body{background:var(--board);font-family:"Outfit",sans-serif;position:relative;color:var(--ink)}
.board-title{position:absolute;top:16px;left:0;width:1200px;text-align:center;color:var(--white);font-weight:700;font-size:50px;letter-spacing:1px}
.board-note{position:absolute;top:78px;left:0;width:1200px;text-align:center;color:var(--white);font-weight:700;font-size:21px;line-height:26px;letter-spacing:.3px}
.screen{position:absolute;width:514px;height:442px;background:var(--white);overflow:hidden}
.hero-photo{position:absolute;left:0;top:0;width:514px;height:345px}
.hero-photo::after{content:"";position:absolute;inset:0;background:linear-gradient(to bottom,rgba(255,255,255,0) 72%,#fff 100%)}
.screen--family .hero-photo{background:linear-gradient(160deg,#8fb7ea 0%,#cfe0f2 35%,#e45a9a 55%,#2d6aa0 70%,#eef3f8 90%)}
.screen--brimwell .hero-photo{background:linear-gradient(180deg,#1f5fbf 0%,#3f86d9 40%,#c9d3e0 60%,#55773f 80%,#8a6b55 100%)}
.screen--road .hero-photo{background:linear-gradient(180deg,#d9835a 0%,#f2b25d 35%,#7d6a52 60%,#4a4e52 85%,#5c6a3c 100%)}
.screen--other .hero-photo{background:linear-gradient(160deg,#cfdce6 0%,#e09c5c 30%,#b8501e 55%,#d8a676 80%,#c0703c 100%)}
.contact-strip{position:absolute;top:9px;left:35px;right:35px;display:flex;justify-content:space-between;font-size:6px;color:var(--white);font-weight:500}
.contact-strip span{display:flex;align-items:center;gap:4px}
.dot-icon{width:11px;height:11px;border-radius:50%;background:var(--white);display:inline-flex}
.nav{position:absolute;left:21px;top:28px;width:471px;height:26px;background:var(--white);border-radius:13px;box-shadow:0 2px 6px rgba(0,0,0,.15);font-size:6.4px;color:var(--nav-text);font-weight:500;white-space:nowrap}
.nav a{position:absolute;top:9px;color:inherit;text-decoration:none}
.nav .home{left:14px;top:8px;color:var(--gold)}
.nav .link-brimwell{left:29px}
.nav .link-family{left:91px}
.nav .link-road{left:136px}
.nav .link-other{left:285px}
.nav .link-about{left:358px}
.nav .contact-btn{left:399px;top:4px;width:62px;height:18px;border-radius:9px;background:var(--gold);color:var(--white);padding:5px 0 0 11px}
.nav .contact-btn i{position:absolute;right:3px;top:3px;width:12px;height:12px;border-radius:50%;background:var(--gold-dark);font-style:normal;text-align:center;line-height:12px;font-size:6px}
.logo{position:absolute;left:218px;top:8px;width:78px;height:68px;background:var(--white);border-radius:34px;border:2px solid #d9c7a3;display:flex;flex-direction:column;align-items:center;justify-content:center;color:var(--teal);font-weight:700;font-size:12px;line-height:12px;text-align:center}
.hero-card{position:absolute;left:30px;top:98px;width:193px;height:175px;color:var(--white);text-align:center}
.hero-card svg{position:absolute;inset:0}
.hero-card .content{position:absolute;left:0;right:0;top:44px}
.hero-card h1{font-size:16px;font-weight:700;line-height:16px;letter-spacing:.2px;white-space:nowrap}
.hero-card p{font-size:7.3px;line-height:8.5px;margin:5px 26px 0}
.hero-card p.lead{font-size:9px;line-height:11px;font-weight:500}
.hero-card .cta{display:inline-block;margin-top:10px;background:var(--gold);color:var(--white);font-size:5.6px;font-weight:700;padding:4px 18px 4px 10px;border-radius:8px;position:relative}
.hero-card .cta::after{content:"↗";position:absolute;right:4px;top:2px;font-size:6px}
.sparkle{position:absolute;left:78px;top:18px;font-size:14px;letter-spacing:3px}
.tiles{position:absolute;left:30px;top:306px;display:flex;gap:8px;list-style:none}
.tile{position:relative;width:108px;height:104px}
.tile svg{position:absolute;inset:0}
.tile span{position:absolute;left:12px;right:12px;bottom:17px;text-align:center;color:var(--white);font-size:7.4px;font-weight:700;line-height:8px;letter-spacing:.2px}
.tile--long span{font-size:6.3px;letter-spacing:0;line-height:7.5px}
.site-footer{position:absolute;left:0;bottom:0;width:514px;height:27px;background:var(--cream);font-size:5.6px;color:var(--ink)}
.site-footer p{position:absolute;left:0;right:0;top:11px;text-align:center}
.social{position:absolute;left:444px;top:8px;display:flex;gap:3px}
.social i{width:10px;height:10px;border-radius:50%;background:var(--teal-dark)}
</style>
</head>
<body>
<svg width="0" height="0" style="position:absolute">
  <defs>
    <linearGradient id="fill-brimwell" x1="0" y1="0" x2="0" y2="1"><stop offset="0" stop-color="#1d5fc4"/><stop offset=".55" stop-color="#7aa6d8"/><stop offset="1" stop-color="#1f5a5a"/></linearGradient>
    <linearGradient id="fill-family" x1="0" y1="0" x2="1" y2="1"><stop offset="0" stop-color="#8fb3e4"/><stop offset=".5" stop-color="#d8508f"/><stop offset="1" stop-color="#1f5a5e"/></linearGradient>
    <linearGradient id="fill-road" x1="0" y1="0" x2="0" y2="1"><stop offset="0" stop-color="#e79a5f"/><stop offset=".45" stop-color="#5c5a4a"/><stop offset="1" stop-color="#1f5457"/></linearGradient>
    <linearGradient id="fill-other" x1="0" y1="0" x2="0" y2="1"><stop offset="0" stop-color="#c45a22"/><stop offset=".5" stop-color="#9a6a48"/><stop offset="1" stop-color="#1f5457"/></linearGradient>
    <path id="tile-shape" d="M12,12 Q54,-4 96,12 Q90,32 104,52 Q90,72 96,92 Q54,108 12,92 Q18,72 4,52 Q18,32 12,12Z"/>
    <path id="hero-shape" d="M30,22 Q70,18 96,1 Q122,18 163,22 Q175,52 192,88 Q175,124 163,153 Q122,157 96,174 Q70,157 30,153 Q18,124 1,88 Q18,52 30,22Z"/>
  </defs>
</svg>

<h1 class="board-title">LANDING PAGE</h1>
<p class="board-note">USER HOVER AN OPTION BELOW TO DYNAMICALLY UPDATE<br>THE BANNER AND NAVIGATE TO ITS PAGE.</p>

<!-- Family trips state -->
<section class="screen screen--family" style="left:97px;top:156px">
  <div class="hero-photo" role="img" aria-label="Family in ski gear cheering on a snowy mountain"></div>
  <div class="contact-strip"><span><i class="dot-icon"></i>hello@rambleandrove.com</span><span><i class="dot-icon"></i>Phone Number (555) 014 2290</span></div>
  <nav class="nav"><a class="home">⌂</a><a class="link-brimwell">Brimwell Vacations</a><a class="link-family">Family Trips</a><a class="link-road">Texas Road Trips</a><a class="link-other">Other Destinations</a><a class="link-about">About Us</a><a class="contact-btn">Contact Us<i>↗</i></a></nav>
  <div class="logo">Ramble<br>&amp; Rove</div>
  <div class="hero-card"><svg viewBox="0 0 193 175" width="193" height="175"><use href="#hero-shape" fill="var(--teal-glass)" stroke="#8fb9b6" stroke-width="1"/></svg><div class="sparkle">+✦+</div>
    <div class="content"><h1>PERFECT FAMILY<br>GETAWAYS</h1><p>Stress-free, fun-filled vacations designed for all ages—because every family deserves time together.</p><span class="cta">PLAN FAMILY TRIP</span></div></div>
  <ul class="tiles">
    <li class="tile tile--long"><svg viewBox="0 0 108 104"><use href="#tile-shape" fill="url(#fill-brimwell)"/></svg><span>BRIMWELL VACATIONS<br>LAND AND SEA</span></li>
    <li class="tile"><svg viewBox="0 0 108 104"><use href="#tile-shape" fill="url(#fill-family)" stroke="var(--gold)" stroke-width="3"/></svg><span>FAMILY<br>TRIPS</span></li>
    <li class="tile"><svg viewBox="0 0 108 104"><use href="#tile-shape" fill="url(#fill-road)"/></svg><span>TEXAS<br>ROAD TRIPS</span></li>
    <li class="tile"><svg viewBox="0 0 108 104"><use href="#tile-shape" fill="url(#fill-other)"/></svg><span>OTHER<br>DESTINATIONS</span></li>
  </ul>
  <footer class="site-footer"><p>© 2026 Ramble &amp; Rove. All Right Reserved</p><div class="social"><i></i><i></i></div></footer>
</section>

<!-- Brimwell state -->
<section class="screen screen--brimwell" style="left:635px;top:156px">
  <div class="hero-photo" role="img" aria-label="Fairytale castle under a bright blue sky"></div>
  <div class="contact-strip"><span><i class="dot-icon"></i>hello@rambleandrove.com</span><span><i class="dot-icon"></i>Phone Number (555) 014 2290</span></div>
  <nav class="nav"><a class="home">⌂</a><a class="link-brimwell">Brimwell Vacations</a><a class="link-family">Family Trips</a><a class="link-road">Texas Road Trips</a><a class="link-other">Other Destinations</a><a class="link-about">About Us</a><a class="contact-btn">Contact Us<i>↗</i></a></nav>
  <div class="logo">Ramble<br>&amp; Rove</div>
  <div class="hero-card"><svg viewBox="0 0 193 175" width="193" height="175"><use href="#hero-shape" fill="var(--teal-glass)" stroke="#8fb9b6" stroke-width="1"/></svg><div class="sparkle">+✦+</div>
    <div class="content"><h1>BRIMWELL VACATIONS<br>LAND &amp; SEA</h1><p>Stress-free, fun-filled vacations designed for all ages—because every family deserves time together.</p><span class="cta">BRIMWELL VACATIONS</span></div></div>
  <ul class="tiles">
    <li class="tile tile--long"><svg viewBox="0 0 108 104"><use href="#tile-shape" fill="url(#fill-brimwell)" stroke="var(--gold)" stroke-width="3"/></svg><span>BRIMWELL VACATIONS<br>LAND AND SEA</span></li>
    <li class="tile"><svg viewBox="0 0 108 104"><use href="#tile-shape" fill="url(#fill-family)"/></svg><span>FAMILY<br>TRIPS</span></li>
    <li class="tile"><svg viewBox="0 0 108 104"><use href="#tile-shape" fill="url(#fill-road)"/></svg><span>TEXAS<br>ROAD TRIPS</span></li>
    <li class="tile"><svg viewBox="0 0 108 104"><use href="#tile-shape" fill="url(#fill-other)"/></svg><span>OTHER<br>DESTINATIONS</span></li>
  </ul>
  <footer class="site-footer"><p>© 2026 Ramble &amp; Rove. All Right Reserved</p><div class="social"><i></i><i></i></div></footer>
</section>

<!-- Texas road trips state -->
<section class="screen screen--road" style="left:97px;top:624px">
  <div class="hero-photo" role="img" aria-label="Open country highway at sunset with a water tower and power lines"></div>
  <div class="contact-strip"><span><i class="dot-icon"></i>hello@rambleandrove.com</span><span><i class="dot-icon"></i>Phone Number (555) 014 2290</span></div>
  <nav class="nav"><a class="home">⌂</a><a class="link-brimwell">Brimwell Vacations</a><a class="link-family">Family Trips</a><a class="link-road">Texas Road Trips</a><a class="link-other">Other Destinations</a><a class="link-about">About Us</a><a class="contact-btn">Contact Us<i>↗</i></a></nav>
  <div class="logo">Ramble<br>&amp; Rove</div>
  <div class="hero-card"><svg viewBox="0 0 193 175" width="193" height="175"><use href="#hero-shape" fill="var(--teal-glass)" stroke="#8fb9b6" stroke-width="1"/></svg><div class="sparkle">+✦+</div>
    <div class="content"><h1>EXEPRIENCE TEXAS<br>ROAD TRIPS</h1><p class="lead">Partnership with Piney Trail Van Rentals</p><span class="cta">START ROAD TRIP</span></div></div>
  <ul class="tiles">
    <li class="tile tile--long"><svg viewBox="0 0 108 104"><use href="#tile-shape" fill="url(#fill-brimwell)"/></svg><span>BRIMWELL VACATIONS<br>LAND AND SEA</span></li>
    <li class="tile"><svg viewBox="0 0 108 104"><use href="#tile-shape" fill="url(#fill-family)"/></svg><span>FAMILY<br>TRIPS</span></li>
    <li class="tile"><svg viewBox="0 0 108 104"><use href="#tile-shape" fill="url(#fill-road)" stroke="var(--gold)" stroke-width="3"/></svg><span>TEXAS<br>ROAD TRIPS</span></li>
    <li class="tile"><svg viewBox="0 0 108 104"><use href="#tile-shape" fill="url(#fill-other)"/></svg><span>OTHER<br>DESTINATIONS</span></li>
  </ul>
  <footer class="site-footer"><p>© 2026 Ramble &amp; Rove. All Right Reserved</p><div class="social"><i></i><i></i></div></footer>
</section>

<!-- Other destinations state -->
<section class="screen screen--other" style="left:634px;top:628px">
  <div class="hero-photo" role="img" aria-label="Two hikers walking beneath a red sandstone rock arch"></div>
  <div class="contact-strip"><span><i class="dot-icon"></i>hello@rambleandrove.com</span><span><i class="dot-icon"></i>Phone Number (555) 014 2290</span></div>
  <nav class="nav"><a class="home">⌂</a><a class="link-brimwell">Brimwell Vacations</a><a class="link-family">Family Trips</a><a class="link-road">Texas Road Trips</a><a class="link-other">Other Destinations</a><a class="link-about">About Us</a><a class="contact-btn">Contact Us<i>↗</i></a></nav>
  <div class="logo">Ramble<br>&amp; Rove</div>
  <div class="hero-card"><svg viewBox="0 0 193 175" width="193" height="175"><use href="#hero-shape" fill="var(--teal-glass)" stroke="#8fb9b6" stroke-width="1"/></svg><div class="sparkle">+✦+</div>
    <div class="content"><h1>EXPLORE OTHER<br>DESTINATIONS</h1><p>From hidden gems to bucket-list destinations, we help you travel anywhere your heart desires.</p><span class="cta">OTHER DESTINATION</span></div></div>
  <ul class="tiles">
    <li class="tile tile--long"><svg viewBox="0 0 108 104"><use href="#tile-shape" fill="url(#fill-brimwell)"/></svg><span>BRIMWELL VACATIONS<br>LAND AND SEA</span></li>
    <li class="tile"><svg viewBox="0 0 108 104"><use href="#tile-shape" fill="url(#fill-family)"/></svg><span>FAMILY<br>TRIPS</span></li>
    <li class="tile"><svg viewBox="0 0 108 104"><use href="#tile-shape" fill="url(#fill-road)"/></svg><span>TEXAS<br>ROAD TRIPS</span></li>
    <li class="tile"><svg viewBox="0 0 108 104"><use href="#tile-shape" fill="url(#fill-other)" stroke="var(--gold)" stroke-width="3"/></svg><span>OTHER<br>DESTINATIONS</span></li>
  </ul>
  <footer class="site-footer"><p>© 2026 Ramble &amp; Rove. All Right Reserved</p><div class="social"><i></i><i></i></div></footer>
</section>
</body>
</html>
```